I need a letterhead for a newsletter that will go out quarterly to the dentists of the 18th district. It is called "The Crestline Digest" We are in Amarillo TX and have this landmark in the photo as our most prominent feature. If it could be used, that would be cool.
This is a professional organization newsletter so the letterhead should be somewhat professional.

Target Market(s)

Dentists

Industry/Entity Type

Dental

Font styles to use
Serif

Colors

Designer to choose only greyscale colors for use in the design.

Requirements
Must have
• I want the title of "The Crestline Digest" to be the on top with the phrase "Cobalt Ridge Dental Society" written underneath.
Nice to have
• the photo incorporated could be incorporated in black and white or color along the bottom of the letterhead or with the title inside the photo.
Should not have
• I don't want it to be cartoony. I want it to be stylish and elegant and professional.

```html
<!DOCTYPE html>
<html lang="en">
<head>
<meta charset="utf-8">
<title>The Crestline Digest – Letterhead</title>
<link href="https://fonts.googleapis.com/css2?family=Cinzel:wght@400;600&family=Didact+Gothic&family=PT+Sans+Narrow&display=swap" rel="stylesheet">
<style>
  :root {
    --backdrop: #e2e2e2;
    --paper: #ffffff;
    --accent: #3a3a3a;
    --accent-soft: #5a5a5a;
    --ink: #2b2b2b;
    --ink-soft: #444444;
    --photo-light: #b8b8b8;
    --photo-mid: #8a8a8a;
    --photo-dark: #4e4e4e;
  }
  * { margin: 0; padding: 0; box-sizing: border-box; }
  html, body { width: 1200px; height: 898px; overflow: hidden; }
  body { background: var(--backdrop); position: relative; }

  .letterhead {
    position: absolute;
    left: 296px; top: 19px;
    width: 608px; height: 860px;
    background: var(--paper);
    box-shadow: 0 6px 24px rgba(0, 0, 0, 0.15);
  }
  .band {
    position: absolute;
    height: 9px;
    background: var(--accent);
  }
  .band--top { top: 0; left: 80px; right: 40px; }
  .band--bottom { bottom: 0; left: 76px; right: 44px; }

  .masthead {
    position: absolute;
    top: 58px; left: 0; right: 0;
    text-align: center;
    color: var(--accent);
    font-family: "Cinzel", serif;
  }
  .masthead__title {
    font-size: 30px;
    font-weight: 600;
    letter-spacing: 0.5px;
    line-height: 1.1;
  }
  .masthead__society {
    font-size: 17px;
    font-weight: 600;
    letter-spacing: 0.6px;
    margin-top: 4px;
    color: var(--accent-soft);
  }

  .contact {
    position: absolute;
    top: 136px; left: 90px; right: 90px;
    border-top: 1.5px solid var(--accent);
    border-bottom: 1.5px solid var(--accent);
    padding: 6px 0 5px;
    font-family: "PT Sans Narrow", sans-serif;
    font-size: 11.5px;
    color: var(--ink);
    text-align: center;
  }
  .contact__row {
    display: flex;
    justify-content: center;
    align-items: center;
    gap: 14px;
    white-space: nowrap;
  }
  .contact__item { display: inline-flex; align-items: center; gap: 5px; }
  .contact__icon { width: 10px; height: 10px; fill: var(--accent); }
  .contact__address { margin-top: 2px; }

  .letter {
    position: absolute;
    top: 232px; left: 76px; right: 70px;
    font-family: "Didact Gothic", sans-serif;
    font-size: 12.6px;
    line-height: 20px;
    color: var(--ink-soft);
  }
  .letter__greeting { margin-bottom: 14px; }
  .letter__para { margin-bottom: 24px; text-align: left; }

  .signature {
    position: absolute;
    top: 612px; right: 68px;
    font-family: "Didact Gothic", sans-serif;
    color: var(--ink-soft);
  }
  .signature__name { font-size: 15px; word-spacing: -2px; }
  .signature__role { font-size: 10.5px; margin-top: 3px; }

  .landmark-photo {
    position: absolute;
    left: 128px; top: 686px;
    width: 232px; height: 140px;
    border: 4px solid var(--accent);
    border-radius: 22px;
    background: linear-gradient(100deg, var(--photo-dark) 0%, var(--photo-mid) 35%, var(--photo-light) 60%, var(--photo-mid) 80%, var(--photo-dark) 100%);
  }
</style>
</head>
<body>
  <main class="letterhead">
    <div class="band band--top"></div>

    <header class="masthead">
      <h1 class="masthead__title">The Crestline Digest</h1>
      <p class="masthead__society">Cobalt Ridge Dental Society</p>
    </header>

    <section class="contact">
      <div class="contact__row">
        <span class="contact__item">
          <svg class="contact__icon" viewBox="0 0 10 10"><path d="M1 4 Q5 0 9 4 L8 5 L6.5 4 L6.5 3 Q5 2.4 3.5 3 L3.5 4 L2 5 Z M2.5 6 L7.5 6 L8.5 9 L1.5 9 Z"/></svg>555.014.2203
        </span>
        <span class="contact__item">
          <svg class="contact__icon" viewBox="0 0 10 10"><path d="M1 4 Q5 0 9 4 L8 5 L6.5 4 L6.5 3 Q5 2.4 3.5 3 L3.5 4 L2 5 Z M2.5 6 L7.5 6 L8.5 9 L1.5 9 Z"/></svg>555.014.7719
        </span>
        <span class="contact__item">
          <svg class="contact__icon" viewBox="0 0 10 10"><rect x="0.5" y="2" width="9" height="6.5"/><path d="M0.8 2.3 L5 5.6 L9.2 2.3" stroke="#fff" stroke-width="0.9" fill="none"/></svg>office@cobaltridgedental.org
        </span>
        <span class="contact__item">
          <svg class="contact__icon" viewBox="0 0 10 10"><circle cx="5" cy="5" r="4.5"/><path d="M0.5 5 H9.5 M5 0.5 V9.5 M5 0.5 Q2 5 5 9.5 M5 0.5 Q8 5 5 9.5" stroke="#fff" stroke-width="0.6" fill="none"/></svg>www.cobaltridgedental.org
        </span>
      </div>
      <p class="contact__address">418 Mesa Vista Dr, Canyon Falls, Randall County 79015, USA</p>
    </section>

    <article class="letter">
      <p class="letter__greeting">Hello Sir/Mam,</p>
      <p class="letter__para">Lorem ipsum dolor sit amet, consectetur adipiscing elit. Donec orci purus, luctus vitae dignissim eu, iaculis sed purus. Vivamus faucibus, ipsum nec aliquet viverra, leo mauris condimentum ligula, sit amet sagittis enim ligula quis arcu. Nam egestas tortor id nisi porttitor mattis. In tortor ante, ultricies in suscipit a, tempus non massa. Vivamus et auctor mi. Fusce vel massa nulla. Phasellus nec eros mauris, et scelerisque orci. Donec malesuada orci vitae nulla accumsan porta a id massa.</p>
      <p class="letter__para">Quisque accumsan iaculis magna sit amet fringilla. Maecenas consequat, magna eget tincidunt semper, odio nibh rutrum mi, id feugiat ante nisi eu risus. Vestibulum nunc orci, rhoncus a placerat in, ultricies in mi. Cras mattis varius eros, vel fringilla nisi suscipit eget. Quisque scelerisque sagittis nulla at porttitor. Mauris a justo et tellus interdum tristique. Sed id augue vitae urna euismod commodo aliquet a quam. Pellentesque arcu velit, cursus et malesuada ut, consequat et diam. Nullam erat sem, rhoncus id ullamcorper vitae, rhoncus et arcu. In ultricies ultricies nulla.</p>
    </article>

    <div class="signature">
      <p class="signature__name">Owen Harlow</p>
      <p class="signature__role">Co-Founder &amp; CEO</p>
    </div>

    <div class="landmark-photo" role="img" aria-label="Black and white photograph of a sandstone rock tower in a canyon under an open sky"></div>

    <div class="band band--bottom"></div>
  </main>
</body>
</html>
```